Local Mortgage Broker requires DL Flyer

I Require DL sized design for local mortgage broker. Content that will go on the flyer is attached along with the logo.
Looking for a bright & catchy design with that little OOMPH.....on the creative side.
Am looking for a responsive campaign with this style of marketing. The main message is that "We may be able to save thousands of dollars for you, just give us a chance to review your mortgages"

Target Market(s)

All home owners with a mortgage or eople looking to buy their first home.

Industry/Entity Type

Marketing

```html
<!DOCTYPE html>
<html lang="en">
<head>
<meta charset="utf-8">
<title>LendWise DL Flyer</title>
<link href="https://fonts.googleapis.com/css2?family=Arimo:ital,wght@0,400;0,700;1,400&display=swap" rel="stylesheet">
<style>
  :root {
    --stage: #6f7073;
    --paper: #ffffff;
    --navy: #2b2a6d;
    --band: #2b2a6d;
    --ink: #1f1f1f;
    --note-ink: #2e2e2e;
    --note-bg: #d4d4d6;
    --photo-light: #f1f0ee;
    --photo-mid: #e1dfdc;
    --photo-warm: #d9c7b8;
  }
  * { margin: 0; padding: 0; box-sizing: border-box; }
  html, body { width: 1200px; height: 636px; overflow: hidden; }
  body { background: var(--stage); font-family: "Arimo", Arial, sans-serif; position: relative; }

  .flyer {
    position: absolute; left: 62px; top: 62px;
    width: 1078px; height: 512px;
    background: var(--paper); overflow: hidden;
  }
  .hero-photo {
    position: absolute; right: 0; top: 0;
    width: 520px; height: 448px;
    background:
      radial-gradient(ellipse at 72% 35%, var(--photo-warm) 0%, rgba(217,199,184,0) 45%),
      linear-gradient(90deg, rgba(255,255,255,1) 0%, var(--photo-light) 30%, var(--photo-mid) 100%);
  }

  .headline {
    position: absolute; left: 46px; top: 40px;
    font-size: 31px; font-weight: 700; color: var(--navy); letter-spacing: -0.2px;
  }
  .intro {
    position: absolute; left: 46px; top: 89px; width: 640px;
    font-size: 16.5px; line-height: 26px; color: var(--ink);
  }

  .services {
    position: absolute; left: 46px; top: 222px;
    display: grid; grid-template-columns: 315px auto; row-gap: 8px;
    list-style: none;
  }
  .services li {
    display: flex; align-items: center; gap: 8px;
    font-size: 18.5px; font-weight: 700; color: var(--navy); white-space: nowrap;
  }
  .services svg { width: 16px; height: 16px; flex: none; }

  .note {
    position: absolute; top: 310px; height: 116px;
    background: var(--note-bg); color: var(--note-ink);
    font-style: italic; font-size: 18.5px; line-height: 25px;
  }
  .note--short { left: 48px; width: 196px; padding: 22px 18px; }
  .note--short::after {
    content: ""; position: absolute; right: -25px; top: 12px;
    border-top: 17px solid transparent; border-bottom: 17px solid transparent;
    border-left: 25px solid var(--note-bg);
  }
  .note--long { left: 282px; width: 396px; padding: 10px 22px; }

  .brand {
    position: absolute; right: 26px; top: 405px;
    display: flex; align-items: center; gap: 8px;
    font-size: 21px; font-weight: 700; color: var(--navy);
  }
  .brand-mark { width: 14px; height: 14px; background: var(--navy); }

  .cta-band {
    position: absolute; left: 0; bottom: 0; width: 100%; height: 64px;
    background: var(--band); color: #fff;
    display: flex; align-items: center; padding-left: 47px;
    font-size: 28px; white-space: nowrap;
  }
  .cta-band strong { font-weight: 700; }
  .cta-band .web { margin-left: 12px; font-weight: 700; }
</style>
</head>
<body>
  <article class="flyer">
    <div class="hero-photo" role="img" aria-label="Hand in a white shirt holding up a house key with a small house-shaped key ring"></div>

    <h1 class="headline">Find the right Finance Solution</h1>
    <p class="intro">Whether you are looking to buy your first home, renovate, refinance or invest, we’re here to negotiate the right finance for you. We’re a one-stop shop with hundreds of loan options available from across Australia’s leading lenders and we’ll work with you to find the right finance solution to meet your needs.</p>

    <ul class="services">
      <li><svg viewBox="0 0 16 16"><path d="M2 2 L14 8 L2 14 Z" fill="none" stroke="#2b2a6d" stroke-width="2" stroke-linejoin="round"/></svg>Refinance existing Mortgage</li>
      <li><svg viewBox="0 0 16 16"><path d="M2 2 L14 8 L2 14 Z" fill="none" stroke="#2b2a6d" stroke-width="2" stroke-linejoin="round"/></svg>Purchase Investment Property</li>
      <li><svg viewBox="0 0 16 16"><path d="M2 2 L14 8 L2 14 Z" fill="none" stroke="#2b2a6d" stroke-width="2" stroke-linejoin="round"/></svg>Purchase First Home</li>
      <li><svg viewBox="0 0 16 16"><path d="M2 2 L14 8 L2 14 Z" fill="none" stroke="#2b2a6d" stroke-width="2" stroke-linejoin="round"/></svg>Upgrade or Renovate existing Property</li>
    </ul>

    <p class="note note--short">The right loan to suit your individual requirements.</p>
    <p class="note note--long">We are confident that we may be able to save you thousands of dollars over the term of your loan by simply reviewing your existing home loan.</p>

    <div class="brand"><span class="brand-mark"></span>LendWise</div>

    <footer class="cta-band">Call us on&nbsp;<strong>0491 570 156</strong>&nbsp;to find out how !<span class="web">www.lendwiseloans.com.au</span></footer>
  </article>
</body>
</html>
```